International Marketing Company - Web Design Project

vRelay is a well-funded start up in London developing an Online Marketing Platform for small businesses in Europe.

We require a large number of high quality business web designs for our business website builder. Our business websites are completely integrated into our Online Marketing systems and therefore it is important for designers to comply with our Design Guidelines.

This initial contest is a trial for us to open up the design process to top designers for the Builders vertical (e.g. Builders, Electricians, Plumbers, Flooring, etc.). We have implemented a base html structure and design and included them in the files.

Use your creativity to design new and fresh designs based on the included elements (e.g. testimonials, business description, etc).

We will award the stated prize money for the top three designs.

Any designers that submit designs we feel are of a high enough quality but do not make the top 3 could still be compensated and WILL be invited to participate in our next vertical competition.

Therefore, we encourage designers to submit as many designs as possible as we may award up to 25 designs.

Submissions will be reviewed daily and feedback provided where possible.

Designers who can also code will have the options to implement their designs for an additional fee.

Good luck!
Updates

There has been a mistake made in regard to the prize. Pixel Harbor should have it fixed soon.

1st place = £350
2nd place = £250
3rd Place = £150

Thanks,
Morris
25/11/2011

UPDATE:

1st place will win £350
2nd place will win £250
3rd place will win £150

Everything else is as to the specification.

Thanks
Morris

Target Market(s)

Builders, Electricians, Plumbers, Tradesman, Small construction companies

Industry/Entity Type

Business

Requirements
Must have
• Totally new designs based around the elements we want to show on each page.

We are looking for something different to the design we already have. But you can use that as a starting point.

Use the included files to see what is required for each page. Here is a brief outline:

Homepage - Testimonials, News, Business Description, Latest Projects and Call to action

About-Us - Team Summary, About the Business and a call to action

Projects Page - Project Details (Oage Title and description), Each project needs a title, content and 2 images.

Testimonials Page - The testifiers name and their comment

Contacts Page - Terrafind Map, Company address, business hours, contact form and a call to action.

Please submit final designs in Photoshop or Fireworks format.

Each page has a set of elements. These element must feature in the design of that page. See supporting documents for page details.

All elements must be included in your design. Please do not add any extra element.

Professional look and feel
Nice to have
• Design variations:
Full width designs
Boxed Designs
With AND without carousels
OR static images
Good use of stock images.

Creative use of the elements, dont be restricted/influenced by the default design we have already

Designs based on the 960 grid

```html
<!DOCTYPE html>
<html lang="en">
<head>
<meta charset="utf-8">
<title>Halden Builders</title>
<link rel="stylesheet" href="https://fonts.googleapis.com/css2?family=Arimo:wght@400;700&family=Cinzel:wght@400;600&family=Libre+Baskerville:ital,wght@1,700&display=swap">
<style>
:root{
  --bg-dark:#8f3f14;
  --bg-mid:#b4581f;
  --page:#ffffff;
  --slate:#474747;
  --ink:#222222;
  --text:#444444;
  --muted:#8a8a8a;
  --orange:#e8731f;
  --panel:#f3f3f3;
  --line:#dddddd;
  --nav-top:#3a3a3a;
  --nav-bot:#050505;
}
*{margin:0;padding:0;box-sizing:border-box}
html,body{width:1159px;height:1200px;overflow:hidden}
body{
  position:relative;
  background:linear-gradient(90deg,var(--bg-dark) 0%,var(--bg-mid) 30%,var(--bg-mid) 70%,var(--bg-dark) 100%);
  font-family:"Arimo",Arial,sans-serif;color:var(--text);
}
.abs{position:absolute}
.page{left:74px;top:14px;width:1011px;height:1186px;background:var(--page)}
.logo-box{left:86px;top:29px;width:230px;height:190px;background:var(--slate)}
.tagline{left:116px;top:248px;font-size:15px;color:#333;word-spacing:3px}
.hero{left:338px;top:29px;width:736px;height:353px;background:var(--slate)}
.header-shadow{left:74px;top:382px;width:1011px;height:8px;background:linear-gradient(#e2e2e2,#fff)}
.nav{left:64px;top:390px;width:1031px;height:49px;background:linear-gradient(var(--nav-top),var(--nav-bot));}
.nav-fold-l,.nav-fold-r{top:382px;width:0;height:0;border-top:8px solid transparent}
.nav-fold-l{left:64px;border-right:10px solid #111}
.nav-fold-r{left:1085px;border-left:10px solid #111}
.nav a{position:absolute;top:16px;color:#fff;text-decoration:none;font-size:16px;font-weight:700;letter-spacing:.3px}
.phone{left:886px;top:399px;display:flex;align-items:center;gap:8px;color:var(--orange);font-size:26px}
.section-head{height:38px;border-bottom:3px solid var(--orange);background:linear-gradient(#fff,#efefef);font-size:21px;color:var(--ink);padding:6px 0 0 18px;letter-spacing:.3px}
.quote{font-size:13px;line-height:20px;color:var(--muted)}
.quote-box{left:88px;top:515px;width:288px;height:100px;background:var(--panel);border:1px solid var(--line);padding:8px 10px}
.signature{left:200px;top:620px;width:168px;text-align:right;font-family:"Libre Baskerville",Georgia,serif;font-style:italic;font-weight:700;font-size:14px;color:#333}
.view-all{left:311px;top:772px;font-size:13px;color:#333}
.welcome-title{left:401px;top:470px;font-size:22px;color:var(--ink);letter-spacing:.3px}
.welcome p{font-size:13px;line-height:23.5px;color:var(--text);margin-bottom:23px}
.cta{left:900px;top:463px;width:176px;height:167px;background:linear-gradient(#fff,#e9e9e9);border:1px solid #e0e0e0;box-shadow:0 6px 6px -4px rgba(0,0,0,.3);text-align:center;font-family:"Cinzel",Georgia,serif;padding-top:30px}
.cta .dark{font-size:22px;line-height:34px;color:#2a2a2a}
.cta .accent{font-size:24px;line-height:36px;color:var(--orange);font-weight:600}
.news{left:86px;top:862px;width:292px;box-shadow:0 6px 6px -4px rgba(0,0,0,.35)}
.news li{list-style:none;height:64px;border-bottom:1px solid #e6e6e6;background:linear-gradient(#fff,#f6f6f6);padding:8px 8px 0 35px;position:relative;font-size:13px;line-height:22px;color:var(--muted)}
.news li svg{position:absolute;left:13px;top:14px}
.projects{left:401px;top:872px;width:673px;height:221px;background:var(--panel);border:1px solid var(--line)}
.thumb{position:absolute;top:22px;width:142px;height:131px;background:#fff;border:1px solid #e2e2e2}
.caption{position:absolute;top:166px;width:160px;text-align:center;font-size:13px;line-height:19px;color:#444}
.footer-line{left:74px;top:1137px;width:1011px;height:1px;background:#e6e6e6}
.footer{left:95px;top:1147px;font-size:13px;color:#aaa;word-spacing:2px}
</style>
</head>
<body>
<div class="abs page"></div>

<header>
  <div class="abs logo-box" role="img" aria-label="Company logo area"></div>
  <div class="abs tagline">Quick . Solid . Quality</div>
  <div class="abs hero" role="img" aria-label="Featured building work image"></div>
  <div class="abs header-shadow"></div>
  <div class="abs nav-fold-l"></div><div class="abs nav-fold-r"></div>
  <nav class="abs nav">
    <a style="left:34px">HOME</a>
    <a style="left:116px">ABOUT US</a>
    <a style="left:230px">TESTIMONIALS</a>
    <a style="left:378px">PORTFOLIO</a>
    <a style="left:502px">CONTACTS</a>
  </nav>
  <div class="abs phone">
    <svg width="20" height="26" viewBox="0 0 20 26"><path d="M5 1 L9 6 L6 9 Q8 15 12 19 L15 16 L19 20 L15 25 Q4 21 1 7 Z" fill="#cfcfcf"/></svg>
    <span>020 7946 0321</span>
  </div>
</header>

<section>
  <div class="abs section-head" style="left:86px;top:466px;width:292px">TESTIMONIALS</div>
  <div class="abs quote-box"><p class="quote">Halden Construction are the best builders in Crawley. They are experts in all areas of house building and I am extremely satisfied with my new loft conversion.</p></div>
  <div class="abs signature">Mr. Petrovane</div>
  <p class="abs quote" style="left:98px;top:672px;width:280px">Halden Construction are the best builders in Crawley. They are experts in all areas of house building and I am extremely satisfied with my new loft conversion.</p>
  <div class="abs view-all">View all</div>
</section>

<section>
  <h1 class="abs welcome-title" style="font-weight:400">WELCOME TO HALDEN BUILDERS</h1>
  <div class="abs welcome" style="left:401px;top:507px;width:490px">
    <p>I am an experienced builder in Crawley, Halden Construction have been based in Crawley for over 10 years. My team and I are proven, reliable builders based in Crawley. We've come across a lot in our time, so don't hesitate to get in touch about any building job in Crawley.</p>
    <p>I am a friendly, handyman who has built a team of excellent tradesmen based in Crawley. My builders in Crawley have years of experience in kitchen renovation, bathroom renovation, roofing and plumbing, loft conversions and house restoration.</p>
    <p>Call Halden Construction on 020 7946 0321 now to discuss how we can help you. My quotes are always FREE with no obligation.</p>
  </div>
  <div class="abs cta">
    <div class="dark">Contact Us</div>
    <div class="dark">for a</div>
    <div class="accent">Quote Now</div>
  </div>
</section>

<section>
  <div class="abs section-head" style="left:86px;top:810px;width:292px">LATEST NEWS:</div>
  <ul class="abs news">
    <li><svg width="6" height="8"><path d="M0 0 L6 4 L0 8Z" fill="#e8731f"/></svg>Halden Construction have just finished another fine job in Crawley.</li>
    <li><svg width="6" height="8"><path d="M0 0 L6 4 L0 8Z" fill="#e8731f"/></svg>Halden Construction have just finished another fine job in Crawley.</li>
    <li><svg width="6" height="8"><path d="M0 0 L6 4 L0 8Z" fill="#e8731f"/></svg>Halden Construction have just finished another fine job in Crawley.</li>
    <li><svg width="6" height="8"><path d="M0 0 L6 4 L0 8Z" fill="#e8731f"/></svg>Halden Construction have just finished another fine job in Crawley.</li>
  </ul>
</section>

<section>
  <div class="abs section-head" style="left:401px;top:810px;width:673px">LATEST PROJECTS</div>
  <div class="abs projects">
    <div class="thumb" role="img" aria-label="Project photo" style="left:18px"></div>
    <div class="caption" style="left:9px">House restoration in Crawley</div>
    <div class="thumb" role="img" aria-label="Project photo" style="left:184px"></div>
    <div class="caption" style="left:175px">House restoration in Crawley</div>
    <div class="thumb" role="img" aria-label="Project photo" style="left:350px"></div>
    <div class="caption" style="left:341px">House restoration in Crawley</div>
    <div class="thumb" role="img" aria-label="Project photo" style="left:515px"></div>
    <div class="caption" style="left:506px">House restoration in Crawley</div>
  </div>
</section>

<footer>
  <div class="abs footer-line"></div>
  <div class="abs footer">home &nbsp;|&nbsp; about us &nbsp;|&nbsp; testimonials &nbsp;|&nbsp; portfolio &nbsp;|&nbsp; contacts</div>
</footer>
</body>
</html>
```